KWT REFRIGERATION HEATING AND COOLING COMPANY IN AUSTRALIA NEEDS A SLEEK AND PROFESSIONAL DESIGN FOR MERALDO VANS THERE DIFFERENT OF VANS AVAILABLE ON THE INTERNET BUT PLEASE USE THIS ONE. (VOLTRA LWB pxm874j french vanilla colour it's without window glass screen). SHOULD BE VERY PLEASING TO SEE AND COLOR SCHEME SHOULD BE GREEN and BLUE OR CLOSE TO OUR LOGO.

THE DESIGN SHOULD COMMUNICATE TO THE PEOPLE AND OUR SERVICES AND CONTACT DETAILS SHOULD BE PROMINENT TO SEE.

ALL POPULAR BRANDS LOGOS NEED TO BE PLACED AS WELL. ( PLS CHECK FLYER) OR READ ALL THE BRIEF.

THE EXISTING COLOR OF THE VAN IS WHITE AND CAN/ SHOULD UTILISE THIS NEGATIVE SPACE/COLOR TO BLEND WITH GREEN AND BLUE. WE WELCOME ANY IMPROVISATION ON COLORS SCHEME.

PS
PLEASE FIND THE ATTACHED DOCUMENTS AND TAKE THE LOGOS FROM THE ORIGINAL WEBSITE AND ALSO SEE BUSINESS CARD AND FLYER

CONTACT

0491738256
0408352147
INFO@KWTREFRIGERTION.EXAMPLE.COM.AU
WWW.KWTREFRIGERATION.EXAMPLE.COM.AU

_________________________________________________
VAN TEXT
CALL ON OUR CREW— TAG LINE
INSTALLATION, REPAIRS , MAINTENANCE , SALE & SERVICE OF DOMESTIC , COMMERCIAL REFRIGERATION HEATING & AIR CONDITIONING
SAME DAY BOOKING/ 24/7

THESE ARE THE HEATER BRANDS

Olmark ( FIND LOGO WEBSITE
TELWOOD ( FIND LOGO WEBSITE
QUISTEL ( FIND LOGO WEBSITE
Harlox ( FIND LOGO WEBSITE
Warm dusk ( FIND LOGO WEBSITE

THESE ARE THE AIR CONS BRAND
Pelvor ( FIND LOGO WEBSITE
Kamorie ( FIND LOGO WEBSITE
TORVANELLA ( FIND LOGO WEBSITE
Quelbrandt ( FIND LOGO WEBSITE
SOLVEK ( FIND LOGO WEBSITE
Dravell ( FIND LOGO WEBSITE
Wx ( FIND LOGO WEBSITE
Nomtu ( FIND LOGO WEBSITE

ACCREDITATION / LOCAL COUNCIL COMPLIANCE AND

AU NUMBER 78519
QPN FIND LOGO ( FIND LOGO WEBSITE
TJR FIND LOGO ( FIND LOGO WEBSITE
Southern Cooling Trades Board FIND LOGO
PIPEWORK GUILD ( FIND LOGO WEBSITE

PLEASE GO THROUGH THE ATTACHED FLYERS TO KNOW WHAT I AM TALKING ABOUT
THANK YOU VERY MUCH FOR YOUR TIME AND EFFORTS TO DESIGN.

Target Market(s)

GENERAL PUBLIC,

Industry/Entity Type

Hvac

Font styles to use
Serif
Sans Serif

Colors
0255a3
9bcb3c
00a990
3277b5

Requirements
Must have
• SEE PROJECT DESCRIPTION
• LEADING AUSTRALIAN BRANDS LOGOS, CONTACT DETAILS,
• OUR COMPANY DETAILS AND LOGOS
Nice to have
• ALL LOGOS CHECK FLYERS,
• SHOULD USE NEGATIVE SPACE AND COLOR
Should not have
• PICTURES, OF ACTUAL PRODUCTS AS IN HEATER AIR CONDITIONING UNITS OR ANY OTHER APPLIANCES

```html
<!DOCTYPE html>
<html lang="en">
<head>
<meta charset="utf-8">
<title>KWT Refrigeration – Rear Door Wrap</title>
<link rel="stylesheet" href="https://fonts.googleapis.com/css2?family=Roboto:wght@500;700&display=swap">
<style>
  :root {
    --page-bg: #d4d7de;
    --van-white: #ffffff;
    --wrap-blue: #2f73dc;
    --wrap-green: #9bcb3c;
    --logo-navy: #16204a;
    --logo-green: #9bcb3c;
    --accent-red: #c4121a;
    --ink: #0c1530;
    --tile-bg: #ffffff;
    --tile-ink: #0255a3;
  }
  * { margin: 0; padding: 0; box-sizing: border-box; }
  html, body { width: 1200px; height: 800px; overflow: hidden; }
  body {
    background: var(--page-bg);
    font-family: "Roboto", Arial, sans-serif;
    position: relative;
  }
  .door-wrap {
    position: absolute;
    left: 300px; top: 35px;
    width: 600px; height: 730px;
    border-radius: 70px 70px 10px 10px;
    overflow: hidden;
    background: var(--van-white);
  }
  .door-wrap svg.bands { position: absolute; inset: 0; }
  .brand-plate {
    position: absolute;
    left: 130px; top: 50px;
    width: 340px; height: 110px;
    padding: 0 22px;
    background: var(--logo-navy);
    border-radius: 18px;
    display: flex; align-items: center; justify-content: center; gap: 14px;
  }
  .brand-plate .brand-dot {
    flex: 0 0 auto;
    width: 20px; height: 20px; border-radius: 50%;
    background: var(--logo-green);
  }
  .brand-plate .brand-name {
    color: var(--logo-green);
    font-weight: 700;
    font-size: 25px;
    letter-spacing: .5px;
    white-space: nowrap;
  }
  .accreditation { position: absolute; left: 63px; top: 262px; }
  .accreditation h2 {
    color: var(--accent-red); font-weight: 700; font-size: 18px; letter-spacing: .3px;
  }
  .accreditation .au-number {
    color: var(--ink); font-weight: 500; font-size: 10px; margin-top: 4px;
  }
  .badge-row { display: flex; gap: 5px; margin-top: 7px; }
  .badge { height: 17px; background: var(--tile-bg); }
  .brand-grid {
    position: absolute; left: 322px; top: 296px;
    display: flex; flex-direction: column; gap: 5px;
  }
  .brand-row { display: flex; gap: 4px; }
  .brand-tile {
    height: 12px; padding: 0 3px;
    background: var(--tile-bg);
    color: var(--tile-ink);
    font-weight: 700; font-size: 7.5px;
    display: flex; align-items: center; justify-content: center;
    white-space: nowrap;
  }
  .brand-tile.tall { height: 16px; }
  .contact-label {
    position: absolute; left: 141px; top: 431px;
    color: var(--accent-red); font-weight: 700; font-size: 15px;
  }
  .phones {
    position: absolute; left: 140px; top: 453px;
    color: var(--ink); font-weight: 700; font-size: 16px; line-height: 18px;
  }
  .web-details {
    position: absolute; left: 302px; top: 454px; width: 296px;
    text-align: center;
    color: var(--ink); font-weight: 700; font-size: 13px; line-height: 18px;
  }
</style>
</head>
<body>
  <main class="door-wrap" aria-label="KWT Refrigeration rear door livery">
    <svg class="bands" width="600" height="730" viewBox="0 0 600 730" aria-hidden="true">
      <polygon points="0,237 300,178 600,237 600,270 300,181 0,270" fill="var(--wrap-green)"/>
      <polygon points="0,270 300,181 600,270 600,730 0,730" fill="var(--wrap-blue)"/>
    </svg>

    <div class="brand-plate">
      <span class="brand-name">KWT REFRIGERATION</span>
      <span class="brand-dot"></span>
    </div>

    <section class="accreditation">
      <h2>ACCREDITATION</h2>
      <p class="au-number">AU NUMBER 78519</p>
      <div class="badge-row">
        <span class="badge" style="width:29px"></span>
        <span class="badge" style="width:42px"></span>
        <span class="badge" style="width:43px"></span>
        <span class="badge" style="width:52px"></span>
      </div>
    </section>

    <section class="brand-grid" aria-label="Brands we service">
      <div class="brand-row">
        <span class="brand-tile">Pelvor</span>
        <span class="brand-tile">Quelbrandt</span>
        <span class="brand-tile">QUISTEL</span>
      </div>
      <div class="brand-row">
        <span class="brand-tile">Harlox</span>
        <span class="brand-tile">Dravell</span>
        <span class="brand-tile">SOLVEK</span>
        <span class="brand-tile">Kamorie</span>
      </div>
      <div class="brand-row">
        <span class="brand-tile tall">Olmark</span>
        <span class="brand-tile tall">Wx</span>
        <span class="brand-tile tall">Nomtu</span>
        <span class="brand-tile tall">Warm dusk</span>
        <span class="brand-tile tall">TORVANELLA</span>
      </div>
      <div class="brand-row">
        <span class="brand-tile tall">TELWOOD</span>
      </div>
    </section>

    <h3 class="contact-label">CONTACT US:</h3>
    <p class="phones">(049) 1738256<br>(040) 8352147</p>
    <p class="web-details">info@kwtrefrigertion.example.com.au<br>www.kwtrefrigeration.example.com.au</p>
  </main>
</body>
</html>
```